Coastline Premier Retreats Business Card Design

Design a business card for Coastline Premier Retreats. Look at the website for colors and reference. Card should have logo, name, title, office number, mobile number, email, URL and a tagline like, "Luxury Hotel & Resort Email Marketing" (This might change).

https://www.coastlinepremierretreats.example

The rest I will leave up to your imagination.

Contact Information for Business Card

Logo, name, title, office number, mobile number, email, URL and a tagline like, "Luxury Hotel & Resort Email Marketing" (This might change).

```html
<!DOCTYPE html>
<html lang="en">
<head>
<meta charset="utf-8">
<title>Coastline Premier Retreats – Business Card</title>
<link href="https://fonts.googleapis.com/css2?family=Montserrat:wght@400;500;600;700&display=swap" rel="stylesheet">
<style>
  :root {
    --backdrop: #2a2a2b;
    --card: #232324;
    --card-deep: #1c1c1d;
    --orange: #f37021;
    --white: #ffffff;
    --muted: #d9d9d9;
    --emboss: #161617;
  }
  * { box-sizing: border-box; margin: 0; padding: 0; }
  html, body { width: 1200px; height: 900px; overflow: hidden; }
  body {
    background: var(--backdrop);
    font-family: "Montserrat", sans-serif;
    position: relative;
  }
  .card {
    position: absolute;
    left: 300px;
    width: 600px;
    height: 340px;
    background: var(--card);
    border-radius: 22px;
    border-bottom: 5px solid var(--orange);
    border-left: 2px solid var(--orange);
    overflow: hidden;
  }
  .card--back { top: 60px; }
  .card--front { top: 470px; }

  .back-mark {
    position: absolute;
    inset: 0;
    display: flex;
    align-items: center;
    justify-content: center;
    gap: 14px;
  }
  .back-mark .mark-square {
    width: 22px; height: 22px;
    background: var(--card-deep);
  }
  .back-mark .mark-name {
    font-weight: 600;
    font-size: 30px;
    color: var(--emboss);
    letter-spacing: 0.5px;
  }

  .front-mark {
    position: absolute;
    left: 34px;
    top: 128px;
    display: flex;
    align-items: center;
    gap: 10px;
  }
  .front-mark .mark-square {
    width: 16px; height: 16px;
    background: var(--orange);
  }
  .front-mark .mark-name {
    font-weight: 600;
    font-size: 17px;
    color: var(--white);
    width: 210px;
    line-height: 1.2;
  }

  .divider {
    position: absolute;
    left: 296px;
    top: 52px;
    width: 1.5px;
    height: 150px;
    background: var(--orange);
  }

  .contact {
    position: absolute;
    left: 314px;
    top: 46px;
    width: 276px;
  }
  .contact .person-name {
    font-weight: 700;
    font-size: 22px;
    color: var(--orange);
    letter-spacing: 0.5px;
  }
  .contact .person-title {
    font-size: 12.5px;
    color: var(--white);
    margin: 2px 0 14px;
  }
  .contact-list { list-style: none; }
  .contact-list li {
    display: flex;
    align-items: center;
    gap: 8px;
    font-size: 10.5px;
    color: var(--muted);
    margin-bottom: 6px;
    white-space: nowrap;
  }
  .contact-list svg { width: 12px; height: 12px; flex: none; }

  .tagline-bar {
    position: absolute;
    left: 384px;
    top: 214px;
    width: 216px;
    height: 36px;
    background: var(--white);
    display: flex;
    align-items: center;
    justify-content: center;
    font-weight: 600;
    font-size: 10.5px;
    color: var(--orange);
  }
  .accent-band {
    position: absolute;
    left: 0;
    top: 250px;
    width: 372px;
    height: 34px;
    background: var(--orange);
  }
</style>
</head>
<body>

  <section class="card card--back" aria-label="Card back">
    <div class="back-mark">
      <span class="mark-square"></span>
      <span class="mark-name">Coastline Premier Retreats</span>
    </div>
  </section>

  <section class="card card--front" aria-label="Card front">
    <div class="front-mark">
      <span class="mark-square"></span>
      <span class="mark-name">Coastline Premier Retreats</span>
    </div>

    <div class="divider"></div>

    <div class="contact">
      <p class="person-name">DANIEL HAYES</p>
      <p class="person-title">Managing Director</p>
      <ul class="contact-list">
        <li>
          <svg viewBox="0 0 12 12"><path d="M1 4 Q6 0 11 4 L9.5 5.5 L8 4.5 L4 4.5 L2.5 5.5 Z M3 6 H9 L10 11 H2 Z" fill="var(--orange)"/></svg>
          555.204.6000
        </li>
        <li>
          <svg viewBox="0 0 12 12"><rect x="3" y="0.7" width="6" height="10.6" rx="1" fill="none" stroke="var(--orange)" stroke-width="1.2"/><circle cx="6" cy="9.5" r="0.7" fill="var(--orange)"/></svg>
          555.318.4970
        </li>
        <li>
          <svg viewBox="0 0 12 12"><rect x="0.5" y="2" width="11" height="8" fill="var(--orange)"/><path d="M0.5 2 L6 6.5 L11.5 2" fill="none" stroke="var(--card)" stroke-width="1"/></svg>
          dhayes@coastlinepremierretreats.example
        </li>
        <li>
          <svg viewBox="0 0 12 12"><circle cx="6" cy="6" r="5.3" fill="var(--orange)"/><path d="M6 0.7 V11.3 M0.7 6 H11.3 M6 0.7 Q2.5 6 6 11.3 M6 0.7 Q9.5 6 6 11.3" fill="none" stroke="var(--card)" stroke-width="0.8"/></svg>
          www.coastlinepremierretreats.example
        </li>
      </ul>
    </div>

    <div class="tagline-bar">Luxury Hotel &amp; Resort Email Marketing</div>
    <div class="accent-band"></div>
  </section>

</body>
</html>
```